Business Card for Vorla Parts Wholesale supplier

Hi There! I need a new business card for our company. We are specialized in selling Vorla parts, mostly we sell new LCD screens for Zelnar and Drelks. I would like to see that back in the design.

You can find the colors and logo's on our website: www.hartuvo.nl

Industry/Entity Type

Business

Contact Information for Business Card

My Details:
Tobias Lindqvist

Phone: 0031687203316
E-mail: Tobias@hartuvo.nl

Slogan: "Because Quality Matters"

Font styles to use
Sans Serif

Colors

Designer to choose colors to be used in the design.

Requirements
Must have
• A Black backside with the Hartuvo logo on it. The front side should be clean with only my contact details.
• But I'm also open for something really different or awesome!
Nice to have
• Remember that we are in the parts & repairing industry, So i'll be handing those business cards mainly to repair companies. Maybe you can do something with that thought :)

```html
<!DOCTYPE html>
<html lang="en">
<head>
<meta charset="utf-8">
<title>Hartuvo Business Card</title>
<link rel="stylesheet" href="https://fonts.googleapis.com/css2?family=Open+Sans:wght@400;600;700&display=swap">
<style>
  :root {
    --stage: #262626;
    --card-white: #ffffff;
    --card-black: #0c0c0c;
    --brand-orange: #f47a20;
    --text-dark: #141414;
    --text-light: #f2f2f2;
    --text-muted: #cfcfcf;
  }
  * { margin: 0; padding: 0; box-sizing: border-box; }
  html, body {
    width: 1200px; height: 950px; overflow: hidden;
    background: var(--stage);
    font-family: "Open Sans", Arial, sans-serif;
  }
  .stage {
    width: 1200px; height: 950px;
    display: flex; flex-direction: column;
    align-items: center; justify-content: center; gap: 60px;
  }
  .card {
    width: 560px; height: 320px;
    position: relative; overflow: hidden;
    box-shadow: 0 18px 40px rgba(0,0,0,0.55);
  }

  /* Front */
  .card-front { background: var(--card-white); display: flex; flex-direction: column; }
  .front-brand {
    flex: 0 0 198px;
    display: flex; align-items: center; justify-content: center;
  }
  .brand-lockup { display: flex; align-items: center; gap: 14px; }
  .brand-mark { width: 40px; height: 40px; background: var(--brand-orange); }
  .brand-name {
    font-weight: 700; font-size: 58px; letter-spacing: 1px; line-height: 1;
    text-transform: lowercase;
  }
  .card-front .brand-name { color: var(--text-dark); }

  .contact-band {
    flex: 0 0 72px; background: var(--card-black);
    display: flex; align-items: center; justify-content: space-between;
    padding: 0 22px;
  }
  .contact-lines { display: flex; flex-direction: column; gap: 6px; }
  .contact-line {
    display: flex; align-items: center; gap: 8px;
    color: var(--text-muted); font-size: 13px; letter-spacing: 0.3px;
  }
  .contact-icon {
    width: 16px; height: 16px; background: var(--brand-orange);
    display: flex; align-items: center; justify-content: center;
  }
  .person { text-align: right; }
  .person-name { color: var(--brand-orange); font-weight: 600; font-size: 18px; line-height: 1.2; }
  .person-email { color: var(--text-light); font-size: 13px; }

  .slogan-band {
    flex: 1; background: var(--brand-orange);
    display: flex; align-items: center; justify-content: flex-end;
    padding: 0 22px;
  }
  .slogan { color: var(--text-light); font-weight: 600; font-size: 15px; letter-spacing: 0.4px; }

  /* Back */
  .card-back {
    background: linear-gradient(150deg, #2b2b2b 0%, #111 35%, #050505 60%, #1d1d1d 100%);
    display: flex; align-items: center; justify-content: center;
  }
  .card-back .brand-name { color: var(--text-light); font-size: 64px; }
  .card-back .brand-mark { width: 44px; height: 44px; }
</style>
</head>
<body>
<main class="stage">
  <section class="card card-front" aria-label="Business card front">
    <div class="front-brand">
      <div class="brand-lockup">
        <span class="brand-mark"></span>
        <span class="brand-name">hartuvo</span>
      </div>
    </div>
    <div class="contact-band">
      <div class="contact-lines">
        <div class="contact-line">
          <span class="contact-icon">
            <svg width="10" height="10" viewBox="0 0 10 10"><path d="M2 1h2l1 2.2-1.2.8a5 5 0 0 0 2.2 2.2l.8-1.2L9 6v2a1 1 0 0 1-1 1A7 7 0 0 1 1 2a1 1 0 0 1 1-1z" fill="#fff"/></svg>
          </span>
          <span>0031687203316</span>
        </div>
        <div class="contact-line">
          <span class="contact-icon">
            <svg width="10" height="8" viewBox="0 0 10 8"><rect x="0.5" y="0.5" width="9" height="7" fill="none" stroke="#fff"/><path d="M0.5 0.8 5 4.5l4.5-3.7" fill="none" stroke="#fff"/></svg>
          </span>
          <span>www.hartuvo.nl</span>
        </div>
      </div>
      <div class="person">
        <div class="person-name">Tobias Lindqvist</div>
        <div class="person-email">Tobias@hartuvo.nl</div>
      </div>
    </div>
    <div class="slogan-band">
      <p class="slogan">Because Quality Matters</p>
    </div>
  </section>

  <section class="card card-back" aria-label="Business card back">
    <div class="brand-lockup">
      <span class="brand-mark"></span>
      <span class="brand-name">hartuvo</span>
    </div>
  </section>
</main>
</body>
</html>
```